Sophisticated, clean website reflecting my feminine, playful side to sell my abstract art,

I need a website no more than 3 pages to showcase my paintings, a little about me and some contact info. I do abstracts so looking for something a little edgy, yet feminine and current.
Updates

Hi there, These are some artists websites that I Iike: Marnelvoss.com (I like how airy it is) peterwallombry.com garethpolvens.com (I like how it scrolls) I'll need a place for a photo ( a headshot-i do not have it yet so I'll need to be able to upload that later) as well as an area for my bio. Also, it's important that I will be able to upload any new photos and descriptions easily so it should be user friendly. Lastly, I like in a sunny place so would like to have this seem upbeat and playful as that is how i like to paint. thanks-I'm trying to upload my photos now -

Target Market(s)

ppl ages 35-70 who want large scale art for their homes

Industry/Entity Type

art

Coding

Coded - Design and coding required

Number of Pages Required

3 page

Colors

Designer to choose colors to be used in the design.

Requirements
Must have
• photos of my art, a place for my bio, be easy to reach me. tasteful-nothing too "in your face" -my clients are pretty high end and organized. They like clean lines
Nice to have
• sophisticated background, muted tones in the back-similar clean font throughout-no cursive
Should not have
• too many dark areas. Too many blocks of color. Too serious.

```html
<!DOCTYPE html>
<html lang="en">
<head>
<meta charset="utf-8">
<title>Helena Marsh — Abstract Art</title>
<link href="https://fonts.googleapis.com/css2?family=Raleway:wght@300;400;600;700&family=Quicksand:wght@400;500&display=swap" rel="stylesheet">
<style>
:root{
  --ink:#1d1d1d;
  --text:#3a3a3a;
  --muted:#6b6b6b;
  --rule:#cfcfcf;
  --bg:#ffffff;
  --footer:#f2f2f2;
  --frame:#e4e4e4;
}
*{box-sizing:border-box;margin:0;padding:0}
html,body{width:1200px;height:2884px;overflow:hidden;background:var(--bg)}
body{position:relative;font-family:"Quicksand",sans-serif;color:var(--text)}
.abs{position:absolute}

/* header */
.brand{display:flex;align-items:center;gap:18px;font-family:"Raleway",sans-serif;font-weight:600;color:var(--ink);letter-spacing:1px;line-height:1}
.brand-mark{width:44px;height:44px;background:var(--ink)}
.site-header .brand{left:0;right:0;top:24px;justify-content:center;font-size:46px}
.main-nav{top:112px;left:0;width:1200px;height:48px}
.main-nav a,.footer-nav a{position:absolute;font-family:"Quicksand",sans-serif;font-size:18px;color:var(--ink);text-decoration:none;letter-spacing:1px}
.main-nav a{top:8px}
.main-nav a.active{border-bottom:2px solid var(--ink);padding-bottom:4px}
.social{display:flex;align-items:center;gap:10px;font-size:16px}
.social-dot{width:30px;height:30px;border-radius:50%;background:var(--ink)}
.header-line{top:158px;left:0;width:1200px;height:1px;background:var(--rule)}

/* hero */
.hero{top:160px;left:0;width:1200px;height:640px;
  background:radial-gradient(circle at 30% 35%,#2e8a55 0,transparent 35%),
             radial-gradient(circle at 75% 60%,#c58d4a 0,transparent 30%),
             radial-gradient(circle at 60% 20%,#1f5c6b 0,transparent 30%),
             linear-gradient(135deg,#d8e6c8,#6fa872 45%,#e4d3b5)}
.arrow{position:absolute;width:40px;height:70px}
.arrow path{fill:none;stroke-width:3}

/* headings */
.section-title{font-family:"Raleway",sans-serif;font-weight:300;font-size:56px;line-height:1;color:var(--ink);letter-spacing:2px}
.title-rule{height:3px;background:var(--ink);width:64px}

/* about */
.portrait{top:860px;left:112px;width:288px;height:500px;background:linear-gradient(180deg,#f3f3f3,#a7bccd 60%,#6d8aa5)}
.about-title{top:962px;left:488px}
.about-rule{top:1030px;left:492px}
.about-copy{top:1062px;left:490px;width:560px;font-size:17px;line-height:25px;color:var(--muted)}
.about-copy p+p{margin-top:14px}

/* gallery */
.gallery-title{top:1490px;left:0;width:1200px;text-align:center}
.gallery-rule{top:1560px;left:568px}
.gallery-frame{top:1620px;left:232px;width:756px;height:460px;border:10px solid var(--frame);box-shadow:0 2px 6px rgba(0,0,0,.25)}
.gallery-art{width:100%;height:100%;background:radial-gradient(circle at 30% 40%,#e9e3ee 0,transparent 25%),radial-gradient(circle at 70% 60%,#3a2f5a 0,transparent 35%),linear-gradient(135deg,#7a6a9a,#b6a3c4 40%,#4d3f6e 75%,#caa478)}

/* contact */
.contact-title{top:2236px;left:0;width:1200px;text-align:center}
.contact-rule{top:2306px;left:568px}
.contact-intro{top:2340px;left:0;width:1200px;text-align:center;font-size:18px;color:var(--ink)}
.contact-row{left:400px;width:400px;display:flex;justify-content:center;align-items:center;gap:14px;color:var(--ink);border-bottom:1px solid var(--rule);padding-bottom:14px}
.contact-row svg{width:30px;height:30px}
.row-phone{top:2412px;font-size:26px}
.row-mail{top:2476px;font-size:20px}
.row-social{top:2530px;font-size:17px;border-bottom:none}

/* footer */
.site-footer{top:2700px;left:0;width:1200px;height:184px;background:var(--footer)}
.site-footer .brand{left:128px;top:40px;font-size:34px;font-weight:700;gap:14px}
.site-footer .brand-mark{width:36px;height:36px}
.footer-nav a{top:50px;font-size:17px}
.copyright{top:128px;left:0;width:1200px;text-align:center;font-size:14px;color:var(--muted)}
</style>
</head>
<body>

<header class="site-header">
  <div class="abs brand"><span class="brand-mark"></span>HELENA MARSH</div>
  <nav class="abs main-nav">
    <a class="active" style="left:184px">HOME</a>
    <a style="left:344px">ABOUT ME</a>
    <a style="left:540px">GALLERY</a>
    <a style="left:726px">CONTACT</a>
    <a class="social" style="left:912px;top:4px"><span class="social-dot"></span>@hemarshart</a>
  </nav>
  <div class="abs header-line"></div>
</header>

<section class="abs hero" role="img" aria-label="Abstract painting in greens, teal and ochre brushstrokes">
  <svg class="arrow" style="left:40px;top:285px" viewBox="0 0 40 70"><path d="M34 4 L6 35 L34 66" stroke="#fff"/></svg>
  <svg class="arrow" style="right:40px;top:285px" viewBox="0 0 40 70"><path d="M6 4 L34 35 L6 66" stroke="#fff"/></svg>
</section>

<section class="about">
  <div class="abs portrait" role="img" aria-label="Headshot of the artist"></div>
  <h2 class="abs section-title about-title">ABOUT ME</h2>
  <div class="abs title-rule about-rule"></div>
  <div class="abs about-copy">
    <p>Lorem ipsum dolor sit amet, consectetur adipiscing elit, sed do eiusmod tempor incididunt ut labore et dolore magna aliqua. Ut enim ad minim veniam, quis nostrud exercitation</p>
    <p>Duis aute irure dolor in reprehenderit in voluptate velit esse cillum dolore eu fugiat nulla pariatur. Excepteur sint occaecat cupidatat non proident, sunt in culpa qui officia deserunt mollit anim id est laborum.Sed ut perspiciatis unde pariatur. Excepteur sint occaecat cupidatat non proident, sunt in culpa qui officia deserunt mollit anim id est laborum.Sed ut perspiciatis unde pariatur. Excepteur sin</p>
  </div>
</section>

<section class="gallery">
  <h2 class="abs section-title gallery-title">PHOTO GALLERY</h2>
  <div class="abs title-rule gallery-rule"></div>
  <svg class="arrow" style="left:150px;top:1820px" viewBox="0 0 40 70"><path d="M34 4 L6 35 L34 66" stroke="#222"/></svg>
  <div class="abs gallery-frame"><div class="gallery-art" role="img" aria-label="Abstract floral painting in violet, cream and gold"></div></div>
  <svg class="arrow" style="left:1010px;top:1820px" viewBox="0 0 40 70"><path d="M6 4 L34 35 L6 66" stroke="#222"/></svg>
</section>

<section class="contact">
  <h2 class="abs section-title contact-title">CONTACT US</h2>
  <div class="abs title-rule contact-rule"></div>
  <p class="abs contact-intro">Please get in touch with me on below details.</p>
  <div class="abs contact-row row-phone">
    <svg viewBox="0 0 24 24"><path d="M6.6 10.8a15 15 0 0 0 6.6 6.6l2.2-2.2a1 1 0 0 1 1-.25 11.4 11.4 0 0 0 3.6.6 1 1 0 0 1 1 1V20a1 1 0 0 1-1 1A17 17 0 0 1 3 4a1 1 0 0 1 1-1h3.5a1 1 0 0 1 1 1c0 1.25.2 2.45.6 3.6a1 1 0 0 1-.25 1z" fill="#222"/></svg>
    (123) 456 7890
  </div>
  <div class="abs contact-row row-mail">
    <svg viewBox="0 0 24 24"><rect x="2.5" y="5" width="19" height="14" fill="none" stroke="#222" stroke-width="1.6"/><path d="M2.5 5 L12 13 L21.5 5" fill="none" stroke="#222" stroke-width="1.6"/></svg>
    helenamarsh@info.com
  </div>
  <div class="abs contact-row row-social">
    <svg viewBox="0 0 24 24"><circle cx="12" cy="12" r="9" fill="none" stroke="#222" stroke-width="1.6"/></svg>
    Follow me on social @hemarshart
  </div>
</section>

<footer class="abs site-footer">
  <div class="abs brand"><span class="brand-mark"></span>HELENA MARSH</div>
  <nav class="footer-nav">
    <a style="left:496px">ABOUT ME</a>
    <a style="left:644px">GALLERY</a>
    <a style="left:788px">CONTACT</a>
    <a class="social" style="left:940px;top:42px"><span class="social-dot"></span>@hemarshart</a>
  </nav>
  <p class="abs copyright">© 2022 Helena Marsh. All Rights Reserved</p>
</footer>

</body>
</html>
```